Corporate Business Card

Very professional, Modern, Not to busy, include phone address email, website
(253) 617-4930, 18761 52nd Avenue S, Kent, WA 98047, martin@plumlinegroup.com, varkoworks.com

Target Market(s)

Manufacturing

Industry/Entity Type

Aero, machining, manufacturing, Off road racing

Contact Information for Business Card

Phone, address email, website

```html
<!DOCTYPE html>
<html lang="en">
<head>
<meta charset="utf-8">
<title>Varko Works – Business Card</title>
<link rel="stylesheet" href="https://fonts.googleapis.com/css2?family=Montserrat:wght@500;800&display=swap">
<style>
  :root {
    --backdrop: #1c1c1c;
    --navy: #16356b;
    --red: #d42129;
    --silver: #c9cbce;
    --ink: #1a1a1a;
    --paper: #ffffff;
  }
  * { margin: 0; padding: 0; box-sizing: border-box; }
  html, body { width: 1200px; height: 927px; overflow: hidden; }
  body {
    background: var(--backdrop);
    font-family: "Montserrat", Arial, sans-serif;
    position: relative;
  }
  .card {
    position: absolute;
    left: 250px;
    width: 700px;
    height: 400px;
    border-radius: 26px;
    overflow: hidden;
  }
  .card--back { top: 50px; background: var(--navy); }
  .card--front { top: 477px; background: var(--paper); }

  .brand {
    position: absolute;
    font-weight: 800;
    letter-spacing: 1px;
    white-space: nowrap;
  }
  .card--back .brand {
    left: 0; right: 0; top: 160px;
    text-align: center;
    font-size: 64px;
    color: var(--silver);
  }
  .card--back .brand-rule {
    position: absolute;
    left: 150px; top: 262px;
    width: 210px; height: 3px;
    background: var(--silver);
  }
  .card--front .brand {
    right: 60px; top: 48px;
    font-size: 40px;
    color: var(--navy);
  }
  .card--front .brand-rule {
    position: absolute;
    right: 250px; top: 112px;
    width: 140px; height: 2px;
    background: var(--navy);
  }

  .address {
    position: absolute;
    left: 50px; top: 150px;
    font-weight: 500;
    font-size: 17px;
    line-height: 1.45;
    color: var(--ink);
  }
  .contacts {
    position: absolute;
    left: 50px; top: 258px;
    list-style: none;
    font-weight: 500;
    font-size: 16px;
    color: var(--ink);
  }
  .contacts li {
    display: flex;
    align-items: center;
    gap: 10px;
    height: 27px;
  }
  .contacts svg { width: 16px; height: 16px; fill: var(--red); flex: none; }

  .edge-band {
    position: absolute;
    left: 0; bottom: 0;
    width: 700px; height: 44px;
  }
</style>
</head>
<body>
  <section class="card card--back" aria-label="Card back">
    <div class="brand">VARKO WORKS</div>
    <div class="brand-rule"></div>
  </section>

  <section class="card card--front" aria-label="Card front">
    <div class="brand">VARKO WORKS</div>
    <div class="brand-rule"></div>

    <p class="address">18761 52nd Avenue<br>S, Kent, WA 98047</p>

    <ul class="contacts">
      <li>
        <svg viewBox="0 0 16 16" aria-hidden="true"><path d="M3.6 1.5l2.3 2.6-1.3 1.9c.9 2 2.4 3.5 4.4 4.4l1.9-1.3 2.6 2.3-1.3 2.3C6.9 15.3.7 9.1 1.3 2.8z"/></svg>
        (253) 617-4930
      </li>
      <li>
        <svg viewBox="0 0 16 16" aria-hidden="true"><path d="M1 3h14v10H1z M1.8 3.8L8 8.6l6.2-4.8" stroke="#fff" stroke-width="1"/></svg>
        martin@plumlinegroup.com
      </li>
      <li>
        <svg viewBox="0 0 16 16" aria-hidden="true"><circle cx="8" cy="8" r="7"/><path d="M1 8h14M8 1c-2.5 2-2.5 12 0 14M8 1c2.5 2 2.5 12 0 14" stroke="#fff" stroke-width="1" fill="none"/></svg>
        www.varkoworks.com
      </li>
    </ul>

    <svg class="edge-band" viewBox="0 0 700 44" aria-hidden="true">
      <polygon points="0,30 478,30 466,44 0,44" fill="var(--navy)"/>
      <polygon points="484,44 500,10 700,0 700,44" fill="var(--red)"/>
    </svg>
  </section>
</body>
</html>
```